Dusty Spur Outfitters Home Page

I need a logo and page design for my home page, maybe some background color suggestions to go with it. I want the logo to project "vintage" and "western wear" but not be your typical trite western saddle and gun type thing.
http://www.dustyspuroutfitters.example/store/cart.php
Not looking for page coding just logo and other design elements to lay in over the site's template to make it "pop"
Reason: Have to finalize the design.
Target Market(s)
My customers are 70/30 men to women.
Industry/Entity Type
Gun

```html
<!DOCTYPE html>
<html lang="en">
<head>
<meta charset="utf-8">
<title>Dusty Spur Outfitters</title>
<link rel="stylesheet" href="https://fonts.googleapis.com/css2?family=Lato:wght@400;700&family=Dancing+Script:wght@700&display=swap">
<style>
  :root {
    --canvas: #d6c3a2;
    --canvas-light: #dccaab;
    --band-edge: #2f2f2e;
    --teal: #3f6265;
    --teal-light: #4d7275;
    --teal-dark: #2f4d50;
    --cream: #eadfc8;
    --field: #e6dcc6;
    --ink: #2d2a26;
    --tagline: #e3d6bc;
  }
  html, body {
    margin: 0;
    padding: 0;
    width: 1200px;
    height: 700px;
    overflow: hidden;
  }
  body {
    background:
      repeating-linear-gradient(45deg, rgba(255,255,255,0.05) 0 1px, transparent 1px 3px),
      repeating-linear-gradient(-45deg, rgba(0,0,0,0.03) 0 1px, transparent 1px 3px),
      linear-gradient(180deg, var(--canvas-light), var(--canvas));
    font-family: "Lato", sans-serif;
    position: relative;
  }
  .header-band {
    position: absolute;
    left: 0;
    top: 268px;
    width: 1200px;
    height: 165px;
    background: var(--band-edge);
    box-shadow: 0 3px 6px rgba(0,0,0,0.25);
  }
  .header-band__texture {
    position: absolute;
    left: 0;
    top: 15px;
    width: 1200px;
    height: 135px;
    background:
      radial-gradient(ellipse at 30% 40%, var(--teal-light), transparent 60%),
      radial-gradient(ellipse at 80% 70%, var(--teal-light), transparent 55%),
      linear-gradient(180deg, var(--teal) 0%, var(--teal-dark) 100%);
  }
  .brand {
    position: absolute;
    left: 58px;
    top: 300px;
    width: 407px;
    display: flex;
    align-items: center;
    gap: 14px;
  }
  .brand__mark {
    width: 22px;
    height: 22px;
    border-radius: 50%;
    background: var(--cream);
    flex: none;
  }
  .brand__name {
    margin: 0;
    font-family: "Lato", sans-serif;
    font-weight: 700;
    font-size: 34px;
    line-height: 1.1;
    color: var(--cream);
    letter-spacing: 1px;
    text-transform: uppercase;
  }
  .tagline {
    position: absolute;
    left: 476px;
    top: 355px;
    margin: 0;
    font-family: "Dancing Script", cursive;
    font-weight: 700;
    font-size: 23px;
    color: var(--tagline);
    text-shadow: 1px 1px 1px rgba(0,0,0,0.45);
    white-space: nowrap;
  }
  .site-search {
    position: absolute;
    left: 901px;
    top: 319px;
    display: flex;
    align-items: center;
    gap: 10px;
  }
  .site-search__field {
    width: 173px;
    height: 30px;
    box-sizing: border-box;
    border: none;
    border-radius: 15px;
    background: var(--field);
    padding: 0 16px;
    font-family: "Lato", sans-serif;
    font-weight: 700;
    font-size: 17px;
    color: var(--ink);
    box-shadow: inset 0 1px 2px rgba(0,0,0,0.25);
  }
  .site-search__field::placeholder { color: var(--ink); }
  .site-search__button {
    border: none;
    background: none;
    padding: 0;
    font-family: "Lato", sans-serif;
    font-weight: 700;
    font-size: 17px;
    color: var(--cream);
    cursor: pointer;
  }
</style>
</head>
<body>
  <header class="header-band">
    <div class="header-band__texture" role="img" aria-label="Weathered teal painted texture"></div>
  </header>

  <div class="brand">
    <span class="brand__mark"></span>
    <h1 class="brand__name">Dusty Spur<br>Outfitters</h1>
  </div>

  <p class="tagline">Brand-New Retro Styled Western Wear</p>

  <form class="site-search" action="http://www.dustyspuroutfitters.example/store/cart.php">
    <input class="site-search__field" type="text" placeholder="Search..." aria-label="Search">
    <button class="site-search__button" type="submit">GO!</button>
  </form>
</body>
</html>
```